Alterations to existing business card

Here is my current logo and I want the "cafe and bar" taken off with just the words Lumo and our slogan "Savour the moment" on the card, Plus the logo.
Our Current Business Card is currently 5.5cm by 5.5cm and would like it to remain like this thanks.
The loyalty card can be 10 squares with the logo specifying the 10th coffee free. I would like the cheapest option please.
Also on our business card would like the Facebook logo and instagram Logo with TAZALUMO27 as link to our photos on instagram.

Keep Colour schemes the same please.

On the business cards

Dale Brinton Director
0427916038
dale27lumo@mailvista.test

Paula Ferrisi Principal
0428571963
paulumo@mailvista.test

Thanks Dale

Industry/Entity Type

Business

```html
<!DOCTYPE html>
<html lang="en">
<head>
<meta charset="utf-8">
<title>Lumo business and loyalty card</title>
<link rel="stylesheet" href="https://fonts.googleapis.com/css2?family=Questrial&display=swap">
<style>
  :root {
    --backdrop: #505050;
    --card: #ffffff;
    --ink: #111111;
    --gold-deep: #eaa23a;
    --gold-light: #f8e27c;
    --gold: #e9a53d;
    --line-green: #6f8a3a;
  }
  * { box-sizing: border-box; margin: 0; padding: 0; }
  html, body { width: 1105px; height: 1200px; overflow: hidden; }
  body {
    background: var(--backdrop);
    font-family: "Questrial", "Century Gothic", sans-serif;
    color: var(--ink);
    position: relative;
  }
  .card {
    position: absolute;
    width: 449px;
    height: 449px;
    background: var(--card);
    overflow: hidden;
  }
  /* front */
  .card-front { left: 124px; top: 110px; }
  .front-band {
    position: absolute; left: 0; top: 0; width: 100%; height: 235px;
    background: linear-gradient(90deg, var(--gold-deep), var(--gold-light));
  }
  .holder-name {
    position: absolute; left: 0; width: 100%; top: 44px;
    text-align: center; font-size: 36px; font-weight: 700; letter-spacing: 0.5px;
    padding-right: 30px; white-space: nowrap;
  }
  .holder-role {
    position: absolute; left: 0; width: 100%; top: 92px;
    text-align: center; font-size: 24px; padding-right: 30px;
  }
  .front-seal {
    position: absolute; left: 143px; top: 140px; width: 162px; height: 162px;
    border-radius: 50%; background: var(--card);
    border: 4px solid var(--gold);
  }
  .front-wordmark {
    position: absolute; left: 0; width: 100%; top: 318px;
    text-align: center; font-size: 76px; line-height: 1; letter-spacing: 2px;
  }
  .front-slogan {
    position: absolute; left: 0; width: 100%; top: 396px;
    text-align: center; font-size: 15px; letter-spacing: 2px;
    color: var(--gold); font-style: italic; white-space: nowrap;
  }
  .front-foot {
    position: absolute; left: 0; bottom: 0; width: 100%; height: 14px;
    background: var(--ink);
  }
  /* back */
  .card-back { left: 500px; top: 630px; }
  .back-mark {
    position: absolute; left: 160px; top: 25px; width: 130px; height: 130px;
    border-radius: 50%; border: 4px solid var(--ink);
    display: flex; align-items: center; justify-content: center;
    font-size: 34px; letter-spacing: 1px;
  }
  .stamps { position: absolute; left: 0; top: 0; }
  .contact {
    position: absolute; left: 0; width: 100%;
    display: flex; align-items: center; justify-content: center; gap: 7px;
    font-size: 20px; color: #333; white-space: nowrap;
  }
  .contact-phone { top: 344px; }
  .contact-email { top: 372px; }
  .contact-social { top: 405px; letter-spacing: 1.5px; }
  .social-dot {
    width: 20px; height: 20px; border-radius: 50%; background: var(--gold);
  }
  .rule { width: 95px; height: 1px; background: linear-gradient(90deg, transparent, var(--line-green)); }
  .rule-right { background: linear-gradient(90deg, var(--line-green), transparent); }
</style>
</head>
<body>

<section class="card card-front">
  <div class="front-band"></div>
  <h1 class="holder-name">DALE BRINTON</h1>
  <p class="holder-role">DIRECTOR</p>
  <div class="front-seal"></div>
  <p class="front-wordmark">LUMO</p>
  <p class="front-slogan">SAVOUR THE MOMENT</p>
  <div class="front-foot"></div>
</section>

<section class="card card-back">
  <div class="back-mark">LUMO</div>

  <svg class="stamps" width="449" height="449" viewBox="0 0 449 449" aria-label="Ten coffee stamps, tenth coffee free">
    <defs>
      <g id="stamp">
        <circle r="31" fill="none" stroke="#111" stroke-width="2"/>
        <circle r="26" fill="none" stroke="#111" stroke-width="3"/>
        <path d="M-13 -2 h20 v7 a9 8 0 0 1 -20 0 z" fill="#111"/>
        <path d="M7 0 a5 4 0 0 1 0 8" fill="none" stroke="#111" stroke-width="2"/>
        <rect x="-15" y="12" width="26" height="2" fill="#111"/>
        <path d="M-6 -6 q-3 -4 0 -8 M-1 -6 q-3 -4 0 -8 M4 -6 q-3 -4 0 -8" fill="none" stroke="#111" stroke-width="1.2"/>
      </g>
    </defs>
    <use href="#stamp" x="81" y="214"/>
    <use href="#stamp" x="153" y="214"/>
    <use href="#stamp" x="225" y="214"/>
    <use href="#stamp" x="297" y="214"/>
    <use href="#stamp" x="369" y="214"/>
    <use href="#stamp" x="81" y="294"/>
    <use href="#stamp" x="153" y="294"/>
    <use href="#stamp" x="225" y="294"/>
    <use href="#stamp" x="297" y="294"/>
    <g transform="translate(369 294)">
      <circle r="31" fill="var(--gold)" stroke="#111" stroke-width="2"/>
      <circle r="27" fill="none" stroke="#c8862a" stroke-width="1"/>
      <text y="7" text-anchor="middle" font-family="Questrial, sans-serif" font-size="19" font-weight="700" fill="#111">FREE</text>
    </g>
  </svg>

  <p class="contact contact-phone">
    <svg width="12" height="20" viewBox="0 0 12 20" aria-hidden="true"><rect x="1" y="1" width="10" height="18" rx="2" fill="none" stroke="var(--gold)" stroke-width="2"/><rect x="4" y="15" width="4" height="1.6" fill="var(--gold)"/></svg>
    <span>0427916038</span>
  </p>
  <p class="contact contact-email">
    <svg width="16" height="11" viewBox="0 0 16 11" aria-hidden="true"><rect width="16" height="11" fill="var(--gold)"/><path d="M0 0 L8 6 L16 0" fill="none" stroke="#fff" stroke-width="1.3"/></svg>
    <span>dale27lumo@mailvista.test</span>
  </p>
  <p class="contact contact-social">
    <span class="rule"></span>
    <span class="social-dot"></span>
    <span>TAZALUMO27</span>
    <span class="rule rule-right"></span>
  </p>
</section>

</body>
</html>
```